New, modern business card for growing audiology practice

We need a new business card for our audiology practice. Our logo and website have recently changed (more modern) and we want our business cards to reflect this change.
We conduct hearing tests, perform earwax removals, and fit & dispense hearing aids to our patients. We are a family owned practice in which the owner is the one who works directly with the patient. I have attached logos in various formats to use, as well as two ideas I found on this website; as well as a scanned copy of our current logo. Good luck!

Industry/Entity Type

Business

Contact Information for Business Card

Company name: Tolvera Hearing Center
Provider name: Peter Wolstenby, Au.D. F/NSB
Phone number: (440) 683-5127
Address: 837 W. Lindell Ave. Harlow Springs, OH 44190
email: tolverahearing@postvane.com
website: tolverahearing.com

Colors
000000
aaaaaa
dbdbdb
cacaca
9bcb3c
afd23c
cadf82
b1b1b1

Requirements
Must have
• My card must include information in the "details" section. In the attached images, I found a few that I liked and I would like to model after - "brisky bouncin'" and "Sound Method Center".
• Must be horizontal.
• Must include logos provided. I uploaded them in various file formats and various ways.
• Must match logo font, if possible, if not, please get as close as you can.
Nice to have
• I really like the idea of having a color on one side with just the logo and company name and the contact information and provider name on the other side. I also really like the idea of having the main color dominating on the logo/company side with accent of that same color on the contact side of the card.
Should not have
• Must not be vertical.

```html
<!DOCTYPE html>
<html lang="en">
<head>
<meta charset="utf-8">
<title>Tolvera Hearing Center – Business Card</title>
<link href="https://fonts.googleapis.com/css2?family=Roboto:wght@400;500;700&display=swap" rel="stylesheet">
<style>
  :root {
    --backdrop: #e9e6e1;
    --card-dark: #1b1c1e;
    --card-light: #f6f6f5;
    --brand-green: #76a83a;
    --ink: #111111;
    --ink-soft: #555555;
    --rule: #444444;
    --white: #ffffff;
  }
  * { margin: 0; padding: 0; box-sizing: border-box; }
  html, body {
    width: 1200px; height: 960px; overflow: hidden;
    background: var(--backdrop);
    font-family: "Roboto", Arial, sans-serif;
  }
  .canvas { position: relative; width: 1200px; height: 960px; }

  .card {
    position: absolute; left: 320px; width: 600px; height: 342px;
    border-radius: 18px;
  }

  /* Front side */
  .card-front { top: 108px; background: var(--card-dark); }
  .front-mark {
    position: absolute; left: 0; right: 0; top: 140px;
    display: flex; align-items: center; justify-content: center; gap: 12px;
    color: var(--brand-green); font-size: 34px; font-weight: 500;
    letter-spacing: 0.5px;
  }
  .mark-dot {
    width: 22px; height: 22px; border-radius: 50%; background: var(--brand-green);
  }
  .front-url {
    position: absolute; left: 0; right: 0; top: 293px;
    text-align: center; color: var(--white);
    font-size: 14px; letter-spacing: 3.4px;
  }

  /* Back side */
  .card-back { top: 493px; background: var(--card-light); }
  .back-mark {
    position: absolute; right: 30px; top: 42px;
    display: flex; align-items: center; gap: 9px;
    color: var(--ink); font-size: 23px; font-weight: 400;
    text-transform: uppercase; letter-spacing: -0.2px;
  }
  .back-mark .mark-dot { width: 14px; height: 14px; }
  .provider-name {
    position: absolute; right: 29px; top: 189px;
    color: var(--brand-green); font-size: 20px; font-weight: 700;
    text-transform: uppercase;
  }
  .provider-title {
    position: absolute; right: 29px; top: 215px;
    color: var(--ink); font-size: 15px; font-weight: 700;
  }
  .divider {
    position: absolute; left: 28px; right: 29px; top: 242px;
    height: 1.5px; background: var(--rule);
  }
  .contact-list {
    position: absolute; left: 28px; top: 256px; list-style: none;
    color: var(--ink-soft); font-size: 14.5px; line-height: 19.5px;
  }
  .contact-list li { display: flex; align-items: center; gap: 8px; }
  .contact-list svg { width: 13px; height: 13px; fill: var(--brand-green); }
  .address {
    position: absolute; right: 28px; top: 275px; text-align: right;
    color: var(--ink-soft); font-size: 14.5px; line-height: 19.5px;
    font-style: normal;
  }
</style>
</head>
<body>
<main class="canvas">
  <section class="card card-front">
    <div class="front-mark"><span class="mark-dot"></span>Tolvera Hearing Center</div>
    <p class="front-url">www.tolverahearing.com</p>
  </section>

  <section class="card card-back">
    <div class="back-mark"><span class="mark-dot"></span>Tolvera Hearing Center</div>
    <p class="provider-name">Peter Wolstenby</p>
    <p class="provider-title">AU.D. F/NSB</p>
    <div class="divider"></div>
    <ul class="contact-list">
      <li>
        <svg viewBox="0 0 16 16" aria-hidden="true"><path d="M3.5 1.5l2.5 0 1.2 3.3-1.6 1.2c.9 1.9 2.4 3.4 4.3 4.3l1.2-1.6 3.3 1.2v2.5c0 1-.8 1.8-1.8 1.8C6.6 14.2 1.8 9.4 1.7 3.3c0-1 .8-1.8 1.8-1.8z"/></svg>
        (440) 683-5127
      </li>
      <li>
        <svg viewBox="0 0 16 16" aria-hidden="true"><path d="M1 3h14v10H1z M1.8 3.6L8 8.6l6.2-5H1.8z" fill-rule="evenodd"/><path d="M1 3l7 5.5L15 3v1.4L8 10 1 4.4z" fill="#f6f6f5"/></svg>
        tolverahearing@postvane.com
      </li>
      <li>
        <svg viewBox="0 0 16 16" aria-hidden="true"><circle cx="8" cy="8" r="7"/><path d="M4 5c1.5 0 2 1 3 1s1 2 0 2.5-1 2 0 3.5M10 3c-.5 1 .5 2 1.5 2s1.5 1 1 2" stroke="#f6f6f5" stroke-width="1.3" fill="none"/></svg>
        tolverahearing.com
      </li>
    </ul>
    <address class="address">837 W. Lindell Ave.<br>Harlow Springs, OH 44190</address>
  </section>
</main>
</body>
</html>
```